Elevating our current Business Card Design

We want to elevate our current business card with a new design to look like a zenith 300 company. We are a premium lubricant distributor (oil and grease).
We need 2 versions, version 1 is as per the uploaded a copy of our current business card with the English version.
For our Chinese version we need to use the front to be English in English and have the back of the card designed exactly like the front for all info to be in Chinese.
The design template needs to be such that we can amend the template with adding different information for each person's card.
The background colour of the card can be changed- we just need to clearly see all information on the card and logos.
The QJR and Ember steady logos cannot have any colour or display changes- only use the logos attached.
All logos need to be included and all information from the attached current card

```html
<!DOCTYPE html>
<html lang="zh-Hant">
<head>
<meta charset="utf-8">
<title>Norva Business Card</title>
<link href="https://fonts.googleapis.com/css2?family=Open+Sans:wght@400;600;700;800&family=Noto+Sans+TC:wght@400;500&display=swap" rel="stylesheet">
<style>
  :root {
    --stage: #232323;
    --card: #f1f1f3;
    --red: #e8312a;
    --ink: #1d1d1d;
    --gold: #e2a72e;
    --orange: #ee7a22;
    --grey: #9a9a9a;
    --green: #1f4b32;
  }
  html, body {
    margin: 0;
    width: 1200px;
    height: 780px;
    overflow: hidden;
    background: var(--stage);
    font-family: "Open Sans", "Noto Sans TC", sans-serif;
  }
  .stage {
    position: relative;
    width: 1200px;
    height: 780px;
  }
  .card {
    position: absolute;
    top: 230px;
    width: 540px;
    height: 320px;
    background: var(--card);
    border-bottom: 4px solid var(--red);
    box-sizing: border-box;
    overflow: hidden;
  }
  .card--front { left: 40px; }
  .card--back { left: 620px; }

  /* brand wordmark */
  .brand {
    display: flex;
    align-items: center;
    color: var(--red);
    font-weight: 800;
    letter-spacing: 2px;
    line-height: 1;
  }
  .brand__dot {
    border-radius: 50%;
    background: var(--gold);
    flex: none;
  }
  .card--front .brand {
    position: absolute;
    left: 50%;
    top: 50%;
    transform: translate(-50%, -50%);
    font-size: 110px;
    gap: 22px;
  }
  .card--front .brand__dot { width: 64px; height: 64px; }

  /* back: name block */
  .person__tab {
    position: absolute;
    right: 0;
    top: 22px;
    width: 10px;
    height: 62px;
    background: var(--red);
  }
  .person {
    position: absolute;
    right: 24px;
    top: 16px;
    text-align: right;
    font-family: "Noto Sans TC", sans-serif;
  }
  .person__name {
    color: var(--red);
    font-size: 32px;
    line-height: 1.15;
  }
  .person__title {
    color: var(--ink);
    font-size: 26px;
    line-height: 1.2;
  }
  .card--back .brand {
    position: absolute;
    left: 34px;
    top: 60px;
    font-size: 56px;
    gap: 12px;
  }
  .card--back .brand__dot { width: 32px; height: 32px; }

  /* back: contact details */
  .address {
    position: absolute;
    left: 34px;
    top: 150px;
    font-family: "Noto Sans TC", sans-serif;
    font-size: 14px;
    line-height: 1.35;
    color: var(--ink);
  }
  .contacts {
    position: absolute;
    left: 34px;
    top: 196px;
    margin: 0;
    padding: 0;
    list-style: none;
    font-size: 14px;
    color: var(--ink);
  }
  .contacts li {
    display: flex;
    align-items: center;
    gap: 8px;
    height: 21px;
  }
  .contacts svg { width: 14px; height: 14px; flex: none; }

  /* back: partner and certificate marks */
  .certs {
    position: absolute;
    right: 22px;
    top: 150px;
    display: flex;
    gap: 18px;
  }
  .cert {
    width: 38px;
    height: 38px;
    border-radius: 50%;
    background: var(--orange);
    box-shadow: 0 0 0 4px var(--card), 0 0 0 7px var(--grey);
  }
  .member {
    position: absolute;
    left: 272px;
    top: 206px;
    font-weight: 700;
    font-size: 14px;
    color: var(--green);
    line-height: 1;
    white-space: nowrap;
  }
  .member small {
    display: block;
    font-size: 7px;
    letter-spacing: 0.5px;
    margin-top: 3px;
  }
  .supplier {
    position: absolute;
    right: 22px;
    top: 222px;
    width: 116px;
    height: 38px;
    border-radius: 5px;
    background: var(--red);
    color: #fff;
    text-align: center;
    font-weight: 800;
    font-size: 16px;
    line-height: 1;
    padding-top: 7px;
    box-sizing: border-box;
  }
  .supplier small {
    display: block;
    font-size: 7px;
    font-weight: 600;
    margin-top: 3px;
    letter-spacing: 0.3px;
  }
  .distributor {
    position: absolute;
    right: 138px;
    top: 240px;
    width: 130px;
    height: 44px;
    border: 1.5px solid var(--red);
    border-right: none;
    border-radius: 5px 0 0 5px;
    display: flex;
    align-items: center;
    gap: 8px;
    padding-left: 8px;
    box-sizing: border-box;
  }
  .distributor .brand { position: static; font-size: 13px; gap: 4px; letter-spacing: 0.5px; }
  .distributor .brand__dot { width: 8px; height: 8px; }
  .distributor__text {
    color: var(--red);
    font-size: 7px;
    font-weight: 600;
    line-height: 1.25;
    white-space: nowrap;
  }
</style>
</head>
<body>
<main class="stage">

  <section class="card card--front" aria-label="Card front">
    <div class="brand"><span class="brand__dot"></span>NORVA</div>
  </section>

  <section class="card card--back" aria-label="Card back">
    <div class="person__tab"></div>
    <div class="person">
      <div class="person__name">瑪拉·柯文</div>
      <div class="person__title">行政主管</div>
    </div>

    <div class="brand"><span class="brand__dot"></span>NORVA</div>

    <div class="address">港灣路48號<br>北岸, 河谷州 5203</div>

    <ul class="contacts">
      <li>
        <svg viewBox="0 0 16 16"><path d="M3 1l3 3-1.5 2a9 9 0 005 5L11.5 9.5l3 3-2 2.5C7 14 2 9 1 3z" fill="#e8312a"/></svg>
        1300 000 412
      </li>
      <li>
        <svg viewBox="0 0 16 16"><rect x="4" y="1" width="8" height="14" rx="1.5" fill="none" stroke="#e8312a" stroke-width="1.4"/></svg>
        +61 400 123 456
      </li>
      <li>
        <svg viewBox="0 0 16 16"><rect x="2" y="6" width="12" height="8" rx="1" fill="#e8312a"/><rect x="5" y="2" width="6" height="5" fill="none" stroke="#e8312a" stroke-width="1.4"/></svg>
        +61 8 9000 2461
      </li>
      <li>
        <svg viewBox="0 0 16 16"><circle cx="8" cy="8" r="6.5" fill="#e8312a"/><path d="M1.5 8h13M8 1.5c-3 3-3 10 0 13M8 1.5c3 3 3 10 0 13" stroke="#fff" stroke-width="1" fill="none"/></svg>
        www.norvalube.com
      </li>
      <li>
        <svg viewBox="0 0 16 16"><rect x="1.5" y="4" width="13" height="9" rx="1" fill="#e8312a"/><path d="M1.5 4.5L8 9.5l6.5-5" stroke="#fff" stroke-width="1.2" fill="none"/></svg>
        mara.corvin@norvalube.com
      </li>
    </ul>

    <div class="certs">
      <span class="cert" role="img" aria-label="Certification badge"></span>
      <span class="cert" role="img" aria-label="Certification badge"></span>
      <span class="cert" role="img" aria-label="Certification badge"></span>
    </div>

    <div class="member">Ember steady<small>NETWORK MEMBER</small></div>

    <div class="distributor">
      <div class="brand"><span class="brand__dot"></span>NORVA</div>
      <div class="distributor__text">NORVA<br>LUBRICANT<br>SUPPLY</div>
    </div>

    <div class="supplier">TAVORA<small>PREMIUM LUBRICANTS</small></div>
  </section>

</main>
</body>
</html>
```